QVN MOONLIT GLOW Party

Hi,
Want to design a flyer for a party.

I have attached a design I would like you to work from and just add in the correct text:

QVN Events presents

November 2013

MOONLIT GLOW
PARTY

DJ COPPER WHISK
VENUE: TBA

DOORS OPEN 8PM

ENTRY STRICTLY OVER 18'S.

DRESS CODE: SMART CASUAL SULTRY SEXY SPRING THREADS

COST: $60 PER HEAD, includes champagne, beer & wine and canapes.

Tickets from www.quillvanenest.example.com.au or 0499 371 582.

```html
<!DOCTYPE html>
<html lang="en">
<head>
<meta charset="utf-8">
<title>QVN Events – Moonlit Glow Party</title>
<link href="https://fonts.googleapis.com/css2?family=Michroma&family=Orbitron:wght@700;900&family=Exo+2:wght@600;700&display=swap" rel="stylesheet">
<style>
  :root {
    --ink: #0b090b;
    --white: #f4f2f6;
    --pink: #d2389c;
    --pink-deep: #a82a7c;
    --lavender: #e4def2;
    --steel-blue: #aeb8d6;
    --metal-dark: #3b3533;
    --metal-light: #c9c0bb;
  }
  * { box-sizing: border-box; margin: 0; padding: 0; }
  html, body { width: 866px; height: 1200px; overflow: hidden; background: var(--ink); }
  .flyer {
    position: relative; width: 866px; height: 1200px; overflow: hidden;
    background: radial-gradient(ellipse at 50% 40%, #1c141b 0%, var(--ink) 70%);
    font-family: "Michroma", sans-serif; color: var(--white);
  }
  .metal-band {
    position: absolute; left: 0; width: 866px; height: 19px;
    background: linear-gradient(90deg, var(--metal-dark), var(--metal-light) 12%, var(--metal-dark) 30%, #6a605c 55%, var(--metal-light) 88%, var(--metal-dark));
  }
  .metal-band--top { top: 0; }
  .metal-band--bottom { bottom: 0; }
  .sponsor-name {
    position: absolute; top: 78px; width: 173px; text-align: center;
    font-size: 15px; line-height: 1.3; color: var(--pink-deep);
  }
  .sponsor-name--left { left: 38px; }
  .sponsor-name--right { left: 655px; }
  .presents {
    position: absolute; top: 54px; left: 0; width: 866px; text-align: center;
    font-size: 21px; font-weight: 400; letter-spacing: 1px;
  }
  .presents strong { font-family: "Orbitron", sans-serif; font-weight: 900; }
  .presents-rule {
    position: absolute; top: 92px; left: 243px; width: 380px; height: 2px;
    background: linear-gradient(90deg, transparent, #9a9a9a, transparent);
  }
  .event-date {
    position: absolute; top: 104px; left: 0; width: 866px; text-align: center;
    font-family: "Orbitron", sans-serif; font-weight: 900; font-size: 27px;
    letter-spacing: 2px; color: var(--pink);
  }
  .hero-art {
    position: absolute; top: 140px; left: 150px; width: 600px; height: 560px;
    background:
      radial-gradient(circle at 62% 40%, rgba(255,255,255,0.75) 0%, rgba(240,170,230,0.55) 14%, transparent 34%),
      radial-gradient(ellipse at 50% 48%, #c03aa8 0%, #8a2f95 35%, #3d1846 60%, transparent 74%);
  }
  .title-main {
    position: absolute; top: 682px; left: 0; width: 866px; text-align: center;
    font-family: "Orbitron", sans-serif; font-weight: 900; font-size: 68px; letter-spacing: 1px;
    color: var(--lavender); text-shadow: -4px 3px 0 #7e6fa2, 0 0 14px rgba(0,0,0,0.6);
  }
  .title-sub {
    position: absolute; top: 760px; left: 0; width: 866px; text-align: center;
    font-size: 40px; font-weight: 400; letter-spacing: 2px; color: transparent;
    -webkit-text-stroke: 1.2px var(--steel-blue);
  }
  .dj-name {
    position: absolute; top: 828px; left: 0; width: 866px; text-align: center;
    font-family: "Orbitron", sans-serif; font-weight: 900; font-size: 27px; letter-spacing: 2px;
    color: var(--pink); -webkit-text-stroke: 0.6px #f3b6dc;
  }
  .venue {
    position: absolute; top: 872px; left: 0; width: 866px; text-align: center;
    font-family: "Exo 2", sans-serif; font-weight: 700; font-size: 24px; letter-spacing: 1px;
  }
  .doors {
    position: absolute; top: 904px; left: 0; width: 866px; text-align: center;
    font-family: "Exo 2", sans-serif; font-weight: 700; font-size: 19px; letter-spacing: 1px;
    color: var(--pink);
  }
  .rule { position: absolute; height: 1.5px; background: var(--pink-deep); }
  .rule--entry { top: 937px; left: 141px; width: 583px; }
  .entry-note {
    position: absolute; top: 948px; left: 0; width: 866px; text-align: center;
    font-size: 20px; letter-spacing: 2px;
  }
  .info-col {
    position: absolute; top: 1000px; font-family: "Exo 2", sans-serif; font-weight: 600;
    font-size: 18px; line-height: 24px; text-transform: uppercase;
  }
  .info-col--dress { right: 459px; text-align: right; }
  .info-col--cost { left: 461px; text-align: left; }
  .info-label { color: var(--pink); }
  .info-label-value { color: var(--white); font-size: 21px; font-weight: 700; }
  .info-col p + p { margin-top: 8px; }
  .info-divider {
    position: absolute; top: 998px; left: 433px; width: 2px; height: 86px; background: var(--pink-deep);
  }
  .rule--tickets-left { top: 1113px; left: 41px; width: 303px; }
  .rule--tickets-right { top: 1113px; left: 525px; width: 301px; }
  .tickets-label {
    position: absolute; top: 1098px; left: 344px; width: 181px; text-align: center;
    font-family: "Exo 2", sans-serif; font-weight: 700; font-size: 24px; color: var(--pink);
  }
  .contact-phone {
    position: absolute; top: 1132px; left: 51px;
    font-family: "Exo 2", sans-serif; font-weight: 700; font-size: 29px; letter-spacing: 1px;
  }
  .contact-web {
    position: absolute; top: 1138px; right: 40px;
    font-family: "Exo 2", sans-serif; font-weight: 700; font-size: 22px;
  }
</style>
</head>
<body>
  <main class="flyer">
    <div class="metal-band metal-band--top"></div>

    <div class="sponsor-name sponsor-name--left">Quillvane Nest</div>
    <div class="sponsor-name sponsor-name--right">Quillvane Nest</div>

    <h2 class="presents">QVN EVENTS <strong>PRESENTS</strong></h2>
    <div class="presents-rule"></div>
    <p class="event-date">NOVEMBER 2013</p>

    <div class="hero-art" role="img" aria-label="Illustration of a DJ wearing headphones amid pink cosmic light, with speakers and two champagne bottles"></div>

    <h1 class="title-main">MOONLIT</h1>
    <p class="title-sub">GLOW PARTY</p>
    <p class="dj-name">DJ COPPER WHISK</p>
    <p class="venue">VENUE: TBA</p>
    <p class="doors">DOORS OPEN 8PM</p>

    <div class="rule rule--entry"></div>
    <p class="entry-note">ENTRY STRICTLY OVER 18'S.</p>

    <section class="info-col info-col--dress">
      <p class="info-label">Dress code:</p>
      <p>Smart casual sultry sexy<br>spring threads</p>
    </section>
    <div class="info-divider"></div>
    <section class="info-col info-col--cost">
      <p><span class="info-label">Cost:</span> <span class="info-label-value">$60 per head</span></p>
      <p>Includes champagne,<br>beer &amp; wine and canapes.</p>
    </section>

    <div class="rule rule--tickets-left"></div>
    <p class="tickets-label">Tickets from:</p>
    <div class="rule rule--tickets-right"></div>

    <p class="contact-phone">ph: 0499 371 582</p>
    <p class="contact-web">www.quillvanenest.example.com.au</p>

    <div class="metal-band metal-band--bottom"></div>
  </main>
</body>
</html>
```